Stylish new business card needed!

Hello everyone! I am in need of a new business card design for an alarm company here in Hurricane WV. I have all fonts, color codes and logos provided for you use! We are a young company and like the style of a clean sleek looking business card. Would like it double sided, one side holding the logo and the other with your design!
Target Market(s)
The people that are looking for the newest tech for home automation and security
Industry/Entity Type
Alarm services; Home automation
Contact Information for Business Card
Name of person; position (Sales; Installer); Phone Number (555.418.7260); Employee cell Number; Website (www.GuardedByVelk.example); Employee Email; Double sided
Look and feel
Each slider illustrates characteristics of the customer's brand and the style your logo design should communicate.

```html
<!DOCTYPE html>
<html lang="en">
<head>
<meta charset="utf-8">
<title>Guarded By Velk – Business Card</title>
<link rel="stylesheet" href="https://fonts.googleapis.com/css2?family=Arimo:wght@400;700&display=swap">
<style>
  :root {
    --backdrop: #232323;
    --card: #1f1f22;
    --card-deep: #1a1a1d;
    --emboss: #2a2a2e;
    --grey: #9c9c9c;
    --orange: #f08a45;
    --white: #f2f2f2;
  }
  * { margin: 0; padding: 0; box-sizing: border-box; }
  html, body {
    width: 1200px; height: 780px; overflow: hidden;
    background: var(--backdrop);
    font-family: "Arimo", Arial, sans-serif;
  }
  .canvas { position: relative; width: 1200px; height: 780px; }

  .card {
    position: absolute;
    width: 540px; height: 309px;
    background: var(--card);
    border-radius: 2px;
    overflow: hidden;
  }
  .card--front { left: 40px; top: 236px; background: var(--card-deep); }
  .card--back  { left: 620px; top: 236px; }

  /* Front: large tone-on-tone name mark */
  .front-mark {
    position: absolute; left: 0; right: 0; top: 92px;
    text-align: center;
    font-weight: 700;
    color: var(--emboss);
    line-height: 1;
  }
  .front-mark__line { display: block; font-size: 22px; letter-spacing: 2px; margin-bottom: 6px; }
  .front-mark__name { display: block; font-size: 96px; letter-spacing: 4px; }
  .front-tagline {
    position: absolute; left: 0; right: 0; top: 222px;
    text-align: center;
    font-size: 9px; font-weight: 700; letter-spacing: 1.5px;
    color: var(--emboss);
  }

  /* Back: vertical decorative name along left edge */
  .side-name {
    position: absolute;
    left: -70px; top: 128px;
    width: 300px;
    transform: rotate(90deg);
    font-size: 92px; font-weight: 700; letter-spacing: 6px;
    color: var(--emboss);
    line-height: 1;
    text-align: center;
  }

  .brand {
    position: absolute; right: 40px; top: 30px;
    width: 230px;
    text-align: center;
    color: var(--grey);
    font-weight: 700;
  }
  .brand__row { display: flex; align-items: center; justify-content: center; gap: 10px; }
  .brand__dot { width: 14px; height: 14px; border-radius: 50%; background: var(--orange); }
  .brand__line { font-size: 15px; letter-spacing: 1.5px; line-height: 1; }
  .brand__name { font-size: 58px; letter-spacing: 3px; line-height: 1; margin-top: 2px; }
  .brand__tagline {
    margin-top: 4px;
    font-size: 7.5px; letter-spacing: 1px;
    color: var(--orange);
  }

  .person {
    position: absolute; right: 52px; top: 152px;
    text-align: right;
  }
  .person__name { font-size: 24px; font-weight: 700; line-height: 1; }
  .person__first { color: var(--orange); }
  .person__last { color: var(--grey); }
  .person__role { font-size: 13px; font-weight: 700; color: var(--white); margin-top: 4px; }
  .accent-bar {
    position: absolute; right: 36px; top: 148px;
    width: 10px; height: 44px;
    background: var(--orange);
  }

  .contacts {
    position: absolute; right: 36px; top: 212px;
    list-style: none;
    text-align: right;
  }
  .contacts li {
    display: flex; align-items: center; justify-content: flex-end; gap: 8px;
    font-size: 12px; line-height: 1; color: var(--white);
    margin-bottom: 6px;
  }
  .contacts svg { width: 11px; height: 11px; flex: none; }
</style>
</head>
<body>
<main class="canvas">

  <section class="card card--front" aria-label="Card front">
    <div class="front-mark">
      <span class="front-mark__line">GUARDED BY</span>
      <span class="front-mark__name">VELK</span>
    </div>
    <p class="front-tagline">AUTOMATION AND SECURITY SERVICES</p>
  </section>

  <section class="card card--back" aria-label="Card back">
    <div class="side-name" aria-hidden="true">VELK</div>

    <div class="brand">
      <div class="brand__line">GUARDED BY</div>
      <div class="brand__row">
        <span class="brand__dot"></span>
        <span class="brand__name">VELK</span>
      </div>
      <div class="brand__tagline">AUTOMATION AND SECURITY SERVICES</div>
    </div>

    <div class="accent-bar"></div>
    <div class="person">
      <div class="person__name"><span class="person__first">Marta</span> <span class="person__last">Kovalik</span></div>
      <div class="person__role">Sales; Installer</div>
    </div>

    <ul class="contacts">
      <li>555.418.7260
        <svg viewBox="0 0 12 12" aria-hidden="true"><path d="M3 1 L5 3.5 L3.8 4.8 Q5 7.2 7.2 8.2 L8.5 7 L11 9 L9.5 11 Q3 10 1 2.5 Z" fill="var(--orange)"/></svg>
      </li>
      <li>555.302.8814
        <svg viewBox="0 0 12 12" aria-hidden="true"><rect x="3" y="0.8" width="6" height="10.4" rx="1" fill="none" stroke="var(--orange)" stroke-width="1.2"/><circle cx="6" cy="9.4" r="0.6" fill="var(--orange)"/></svg>
      </li>
      <li>www.GuardedByVelk.example
        <svg viewBox="0 0 12 12" aria-hidden="true"><circle cx="6" cy="6" r="5" fill="none" stroke="var(--orange)" stroke-width="1.1"/><ellipse cx="6" cy="6" rx="2.2" ry="5" fill="none" stroke="var(--orange)" stroke-width="1"/><line x1="1" y1="6" x2="11" y2="6" stroke="var(--orange)" stroke-width="1"/></svg>
      </li>
      <li>info@GuardedByVelk.example
        <svg viewBox="0 0 12 12" aria-hidden="true"><rect x="0.8" y="2.5" width="10.4" height="7.5" fill="none" stroke="var(--orange)" stroke-width="1.1"/><path d="M0.8 2.5 L6 6.8 L11.2 2.5" fill="none" stroke="var(--orange)" stroke-width="1.1"/></svg>
      </li>
    </ul>
  </section>

</main>
</body>
</html>
```